Life Coaching business needs a new flyer

We are an Australian business that specialises in Life Coaching, Career Coaching, Health and Wellness Coaching, Yoga and Pilates. We need a A4 double sided flyer that is full colour and folded to DL format. I have attached a couple of designs that I like and some pictures and would like the flyer to be bright yet stylish.

Industry/Entity Type

Life Coaching

```html
<!DOCTYPE html>
<html lang="en">
<head>
<meta charset="utf-8">
<title>Brightpath Coaching – DL Flyer</title>
<link href="https://fonts.googleapis.com/css2?family=Source+Sans+3:ital,wght@0,400;0,600;1,600&display=swap" rel="stylesheet">
<style>
:root{
  --blue:#1f6db4;
  --blue-deep:#15569a;
  --green:#6cb33f;
  --text:#6d6e71;
  --sky:#dcedf8;
  --sky-soft:#eef6fc;
  --panel-grey:#eeeff0;
  --backdrop:#e5e5e7;
}
*{margin:0;padding:0;box-sizing:border-box}
html,body{width:877px;height:1200px;overflow:hidden;background:var(--backdrop)}
body{font-family:"Source Sans 3",Arial,sans-serif;color:var(--text)}
.stage{position:absolute;left:0;top:0;width:1001px;height:1369px;transform:scale(.8761);transform-origin:0 0;border:1px solid #9a9a9c;background:var(--backdrop)}
.sheet{position:absolute;left:79px;width:842px;height:596px;background:#fff;box-shadow:3px 4px 8px rgba(0,0,0,.35);overflow:hidden}
.sheet--outer{top:52px}
.sheet--inner{top:693px;height:595px}
.panel{position:absolute;top:0;height:100%;width:281px}
.panel--1{left:0}.panel--2{left:280px}.panel--3{left:561px}
.bg-sky{background:linear-gradient(180deg,#fff 0%,var(--sky-soft) 45%,var(--sky) 100%)}
.bg-grey{background:linear-gradient(180deg,var(--panel-grey) 0%,var(--panel-grey) 60%,#fff 100%)}
.bg-white{background:linear-gradient(180deg,#fff 0%,#f3f8fc 100%)}
.photo,.waves{position:absolute;left:0;top:0;width:842px;height:100%}
.waves{pointer-events:none}
.txt{position:absolute;font-size:9.6px;line-height:12px}
h2,h3{color:var(--blue);font-weight:600}
h2{font-size:13.5px;line-height:16px}
h3{font-size:13px;line-height:15px}
p{text-align:justify}
.quote{margin-bottom:12px}
.center{text-align:center}
.brand{position:absolute;text-align:center;color:var(--blue);font-weight:400;letter-spacing:.5px}
.brand-dot{display:block;margin:0 auto 6px;border-radius:50%;background:var(--green)}
.offer{position:absolute;left:319px;top:291px;width:193px;height:48px;border:1.5px solid #4d9bd8;border-radius:6px;background:#fff;font-size:9px;line-height:12px;color:#444;font-weight:600;text-align:center;padding-top:5px}
.contact{position:absolute;left:280px;width:281px;text-align:center;white-space:nowrap}
.contact--tag{font-size:7.5px;line-height:10px;color:var(--blue);font-weight:600}
.contact--phone{color:var(--blue);font-size:13px;line-height:15px;font-weight:600}
.contact--email{color:var(--blue-deep);font-size:10.5px;line-height:13px;font-weight:600}
.contact--web{font-size:9px;line-height:12px;color:#555}
.web{color:var(--blue);font-size:13.5px;font-weight:600}
.ticks{list-style:none}
.ticks li{position:relative;padding-left:12px;margin-bottom:5px;font-size:9.6px;line-height:11px}
.ticks li::before{content:"";position:absolute;left:0;top:2px;width:7px;height:7px;border-radius:50%;background:var(--green)}
.tight li{margin-bottom:3px}
.answer{color:var(--green);font-style:italic;font-weight:600;font-size:13px;line-height:15px}
.seal{position:absolute;left:167px;top:354px;width:92px;height:92px;border-radius:50%;background:#fff;box-shadow:0 2px 6px rgba(0,0,0,.3);display:flex;align-items:center;justify-content:center;text-align:center;color:var(--blue);font-size:11px;line-height:13px;font-weight:400}
</style>
</head>
<body>
<div class="stage">

  <section class="sheet sheet--outer">
    <div class="panel panel--1 bg-sky"></div>
    <div class="panel panel--2 bg-grey"></div>
    <div class="panel panel--3 bg-white"></div>

    <svg class="photo" viewBox="0 0 842 596" role="img" aria-label="Photo of a group of happy friends at a seaside lookout at sunset">
      <defs><linearGradient id="sunset" x1="0" y1="0" x2="0" y2="1"><stop offset="0" stop-color="#f4d29a"/><stop offset=".5" stop-color="#c98a5c"/><stop offset="1" stop-color="#6e5748"/></linearGradient></defs>
      <path d="M0,418 C90,388 190,395 280,405 L280,596 L0,596Z" fill="url(#sunset)"/>
    </svg>
    <svg class="photo" viewBox="0 0 842 596" role="img" aria-label="Photo of a joyful woman standing in a pink convertible under a blue sky">
      <defs><linearGradient id="skycar" x1="0" y1="0" x2="0" y2="1"><stop offset="0" stop-color="#5fb4ec"/><stop offset=".6" stop-color="#9fd2f2"/><stop offset="1" stop-color="#e06aa4"/></linearGradient></defs>
      <path d="M561,186 C650,200 760,176 842,140 L842,455 C760,488 650,482 561,472Z" fill="url(#skycar)"/>
    </svg>

    <svg class="waves" viewBox="0 0 842 596" aria-hidden="true">
      <path d="M0,398 C90,366 190,376 280,392 L280,408 C190,398 90,394 0,424Z" fill="var(--green)"/>
      <path d="M0,432 C90,402 190,404 280,414" fill="none" stroke="var(--blue)" stroke-width="3"/>
      <path d="M561,168 C650,190 760,160 842,122 L842,142 C760,178 650,204 561,190Z" fill="var(--blue)"/>
      <path d="M561,192 C650,206 760,182 842,146" fill="none" stroke="var(--green)" stroke-width="3"/>
      <path d="M380,470 C450,482 520,500 600,496 C700,490 780,470 842,448 L842,596 L561,596 L561,500 C500,505 440,490 380,470Z" fill="#fff" opacity=".9"/>
      <path d="M380,468 C450,480 520,498 600,494 C700,488 780,468 842,446" fill="none" stroke="var(--blue)" stroke-width="5"/>
      <path d="M561,484 C660,492 760,478 842,432 L842,444 C760,492 660,502 561,494Z" fill="var(--green)"/>
    </svg>

    <svg class="photo" viewBox="0 0 842 596" role="img" aria-label="Round portrait photo of the two coaches">
      <circle cx="418" cy="430" r="72" fill="#2f82c4"/>
      <circle cx="418" cy="430" r="66" fill="#8a7a70"/>
    </svg>

    <div class="txt" style="left:28px;top:30px;width:226px">
      <h2 style="margin-bottom:6px">Happy Clients Testimonials</h2>
      <p class="quote">“I have lost 10 kilos and now have the energy to play with my kids. Thanks Mara for you support/guidance and helping me get rid of my limiting beliefs. I feel I can achieve anything now! The sky’s the limit”<br>Tessa, Mosman</p>
      <p class="quote">“I had always wanted to start up own café however every time it came to putting it into practice I would procrastinate and not achieve anything. I became overwhelmed with the whole process and never achieved anything. Mara put it into bite sized chunks and helped me to set small achievable go als. I am now a happy café owner.”<br>Jodie, Double Bay</p>
      <p class="quote">“Mara has helped to change my life around in all aspects. I would have been lost without her. Thanks Mara for your professionalism, support and guidance.”<br>Carla, Cremorne</p>
      <p class="quote">“I was so busy with kids, work, and my husband I lost who I was. Mara has helped me find the person I am again.”<br>Renee, Chatswood</p>
    </div>

    <div class="brand" style="left:280px;top:106px;width:281px;font-size:11px">
      <span class="brand-dot" style="width:26px;height:26px"></span>Brightpath Coaching
    </div>
    <div class="txt center" style="left:300px;top:184px;width:241px">
      <p class="center">Brightpath Coaching and Meditation Studio is a professional service that can help you achieve the goals that you are looking for in Life Coaching, Meditation, and Yoga/Pilates</p>
      <p class="center" style="margin-top:12px">If you are ready to take your life to the next level and would like to know more, please contact us</p>
    </div>
    <div class="offer">Free Introductory Life Coaching<br>Phone/Skype session -20 mins<br>(To see if coaching is right for you)</div>

    <div class="contact contact--tag" style="top:513px">LIFE COACHING • MEDITATION • YOGA/PILATES</div>
    <div class="contact contact--phone" style="top:527px">
      <svg width="11" height="11" viewBox="0 0 12 12" aria-hidden="true" style="vertical-align:-1px"><circle cx="6" cy="6" r="5.3" fill="none" stroke="var(--blue)" stroke-width="1.2"/><path d="M4,3.3 L5,3 5.5,4.6 4.9,5 C5.3,6 6,6.7 7,7.1 L7.4,6.5 9,7 8.7,8 C6.4,8.2 3.8,5.6 4,3.3Z" fill="var(--blue)"/></svg>
      02 9000 4127</div>
    <div class="contact contact--email" style="top:546px">hello@brightpathstudio.com.au</div>
    <div class="contact contact--web" style="top:562px">www.brightpathstudio.com.au</div>

    <div class="brand" style="left:561px;top:28px;width:281px;font-size:19px">
      <span class="brand-dot" style="width:44px;height:44px"></span>Brightpath Coaching
      <span style="display:block;font-size:7.5px;color:var(--green);letter-spacing:1px;margin-top:1px">AND MEDITATION STUDIO</span>
    </div>
    <div class="txt center" style="left:561px;top:534px;width:281px;font-size:10px">Life Coaching • Meditation • Yoga/Pilates</div>
    <div class="txt center web" style="left:561px;top:555px;width:281px">www.brightpathstudio.com.au</div>
  </section>

  <section class="sheet sheet--inner">
    <div class="panel panel--1 bg-white"></div>
    <div class="panel panel--2 bg-white"></div>
    <div class="panel panel--3 bg-sky"></div>

    <svg class="photo" viewBox="0 0 842 595" role="img" aria-label="Photo of a smiling senior couple sitting on the bow of a yacht">
      <defs><linearGradient id="sea" x1="0" y1="0" x2="0" y2="1"><stop offset="0" stop-color="#7fb8e6"/><stop offset=".6" stop-color="#2e6fb0"/><stop offset="1" stop-color="#1d4f86"/></linearGradient></defs>
      <path d="M0,160 C90,138 200,120 280,116 L280,392 C200,398 90,430 0,458Z" fill="url(#sea)"/>
    </svg>
    <svg class="photo" viewBox="0 0 842 595" role="img" aria-label="Photo of a woman holding a yoga balance pose by the sea">
      <path d="M280,0 H561 V50 C470,85 370,98 280,100Z" fill="#9ccbec"/>
    </svg>
    <svg class="photo" viewBox="0 0 842 595" role="img" aria-label="Photo of a group meditating cross-legged on a lawn by the water">
      <defs><linearGradient id="lawn" x1="0" y1="0" x2="0" y2="1"><stop offset="0" stop-color="#a9cfee"/><stop offset=".45" stop-color="#8bb6d6"/><stop offset=".6" stop-color="#7e9a4a"/><stop offset="1" stop-color="#5f7d33"/></linearGradient></defs>
      <path d="M280,410 C370,400 470,410 561,440 V595 H280Z" fill="url(#lawn)"/>
    </svg>
    <svg class="photo" viewBox="0 0 842 595" role="img" aria-label="Photo of a couple doing a tree pose on the beach">
      <defs><linearGradient id="beach" x1="0" y1="0" x2="0" y2="1"><stop offset="0" stop-color="#d8e7f2"/><stop offset=".55" stop-color="#c7dbe8"/><stop offset="1" stop-color="#e8dfcf"/></linearGradient></defs>
      <path d="M561,250 C650,276 760,266 842,215 V452 C760,470 650,464 561,456Z" fill="url(#beach)"/>
    </svg>

    <svg class="waves" viewBox="0 0 842 595" aria-hidden="true">
      <path d="M0,136 C90,120 200,104 280,100 L280,118 C200,122 90,142 0,162Z" fill="var(--green)"/>
      <path d="M280,100 C370,98 470,85 561,50 V66 C470,100 370,112 280,116Z" fill="var(--green)"/>
      <path d="M561,226 C650,258 760,250 842,192 V214 C760,266 650,276 561,250Z" fill="var(--blue)"/>
      <path d="M0,460 C100,428 200,396 300,398 C420,402 480,438 561,454 C650,470 760,462 842,430 V595 H561 V470 C480,455 420,418 300,414 C200,412 100,445 0,478Z" fill="var(--sky-soft)"/>
      <path d="M0,458 C100,426 200,394 300,396 C420,400 480,436 561,452 C650,468 760,460 842,428" fill="none" stroke="var(--blue)" stroke-width="6"/>
      <path d="M0,480 C100,448 200,416 300,418" fill="none" stroke="var(--blue)" stroke-width="2" opacity=".5"/>
    </svg>
    <div class="panel panel--3" style="top:470px;height:125px;background:linear-gradient(180deg,var(--sky-soft),var(--sky))"></div>
    <div class="panel panel--1" style="top:480px;height:115px;background:linear-gradient(180deg,var(--sky-soft),var(--sky))"></div>

    <div class="txt" style="left:12px;top:16px;width:260px">
      <ul class="ticks">
        <li>Are you looking at making changes this year?</li>
        <li>Are you stuck in a rut or at a crossroad in your life?</li>
        <li>Are you wanting to lose weigh but can’t get motivated?</li>
        <li>Do you have ongoing problems with your career, relationships, or just life itself?</li>
      </ul>
      <div class="answer" style="margin-top:12px">Life coaching is the answer!</div>
    </div>
    <div class="seal">Brightpath<br>Coaching</div>
    <div class="txt" style="left:13px;top:468px;width:252px">
      <h3 style="margin-bottom:4px">Brightpath Coaching and Meditation Studio</h3>
      <p>Our mission is to help you become the best possible person you can be. Mentally, physically, and spiritually. We offer highly qualified and compassionate trainers/coaches for Life Coaching, Meditation, Yoga and Pilates.<br>They will guide and motivate you every step of the way to achieve all your dreams and goals. They will make you be the best you can be!</p>
    </div>

    <div class="txt" style="left:293px;top:121px;width:252px">
      <h3>Life Coaching</h3>
      <p>Your Life Coach will give you the confidence and the ability to move forward in a positive manner in all areas of your life where you crave change. Life Coaching is about breaking down the barrierspreventing this change from happening, and creating the ideal environment for positive action to take place. It is a holistic approach, which looks at the present and sets goals for a totally successful future.</p>
      <h3 style="margin-top:6px">Career Coaching</h3>
      <p>Are you at a crossroads in your career and at a loss about what to do next? Do you want your work to be in alignment with the authentic you? It can be difficult to assess career options, goals, and strategies, and have the confidence to implement changes on your own. With the right coaching support, you will gain the clarity that you need to take control and have a fulfilling and rewarding career.</p>
      <h3 style="margin-top:6px">Wellness Coaching</h3>
      <p>Health and wellness coaches help their clients find the motivation and tools to achieve their health and wellness goals, working with the client to examine and improve the psychological framework that supports those goals.</p>
    </div>

    <div class="txt" style="left:573px;top:12px;width:256px">
      <h3>Why Would I Need Help?</h3>
      <p style="text-align:left">Coaching is for anyone who wants to make lasting changes in their life.</p>
      <p style="text-align:left;margin:3px 0 5px">Coaching can assist with such issues as:</p>
      <ul class="ticks tight">
        <li>Creating a better work - life balance</li>
        <li>Resolving relationship issues</li>
        <li>Career guidance</li>
        <li>Stress management</li>
        <li>Weight loss and fitness</li>
        <li>Motivation and goal setting</li>
        <li>Boosting your self esteem</li>
        <li>Overcoming negative emotions and thoughts</li>
        <li>Better time management</li>
      </ul>
    </div>
    <div class="txt" style="left:576px;top:477px;width:250px">
      <h3>Meditation</h3>
      <p>We specialise in teaching meditation from beginners to advanced and teach a variety of techniques for stress reduction, peace of mind, stillness, and clarity.</p>
      <h3 style="margin-top:4px">Yoga/Pilates</h3>
      <p>Your highly qualified and experienced Yoga or Pilates instructor will come to you and create a fun and varied workout based on what you enjoy and what your goals are.</p>
    </div>
  </section>

</div>
</body>
</html>
```